Security and Technology Website - Bold and Confident, Something Unexpected

Maple Wren Systems is launching its first website and we need a great design to bring our brand to life and generate DTC and B2B leads.

We have a good logo, but I am struggling with the creative vision to bring it all together. While our industry is Alarm Systems and Technology, we want to create a site that is more friendly and less 'typical' than your standard IT sites.

It Must:
1. Appeal to both men and women. The logo is a bit masculine, so the colors and icons must soften this.
2. Feel modern - we need to convey that we we use the latest technology.
3. Feel a bit high-end. We are not a budget solution.
4. Have a distinct iconography and photo treatment.
5. Feel layered - not just a series of stacked horizontal modules.

It Should Not:
1. Feel like your typical IT website.

Here are resources to get you started!
• Staging Site:
https://maple-wren-systems.shopfrontdemo.example/
Password: Piper

•Brand Guide: https://www.layoutboard.example/design/QKRmWpLcT4V/hNbq8Yf2-ZsKeRtDw7xp-QE/edit?utm_content=QKRmWpLcT4V&utm_campaign=designshare&utm_medium=link2&utm_source=sharebutton

• Logo and Fonts and Photos: :https://files.cloudlocker.example/folders/7HtPqWmZc3Kd9RbLx2VnYs8FgJe4UoAiT?usp=sharing

• Design Inspiration (don't feel limited by this): https://www.layoutboard.example/design/QKTnHsVbWe8/p7MfRz31xYqLcKdTu9GNBw/edit?utm_content=QKTnHsVbWe8&utm_campaign=designshare&utm_medium=link2&utm_source=sharebutton

______________

The winner will be asked to provide design files and finished PNGs of the overall design file, backgrounds, photo treatments/frames, and icons.

The winner will likely be engaged for a phase 2 to build out a product page.

Industry/Entity Type

Alarm Systems, Home Theatres, and Commercial IT Networking

Number of Pages Required

1 page

Font styles to use
Sans Serif

Colors
0054AA
0677BA
7BADD7
CADEEF
E8F1F8
0094D4
00A9DD
6FCCEA
C7EBF8
E9F6FB
EB3D1F
EC4F4E
F09395
F8D3D4
FCEDEE

Requirements
Must have
• 1. Appeal to both men and women. The logo is a bit masculine, so the colors and icons must soften this. 2. Feel modern - we need to convey that we we use the latest technology. 3. Feel a bit high-end. We are not a budget solution. 4. Have a distinct iconography and photo treatment. 5. Feel layered - not just a series of stacked horizontal modules.
Should not have
• 1. Should not feel like just another IT website.

```html
<!DOCTYPE html>
<html lang="en">
<head>
<meta charset="utf-8">
<title>Maple Wren Systems — Safer. Smarter. Faster.</title>
<link rel="stylesheet" href="https://fonts.googleapis.com/css2?family=Saira:ital,wght@0,400;0,500;0,600;0,800;0,900;1,800&family=Open+Sans:ital,wght@0,400;0,600;0,700;1,400;1,700&display=swap">
<style>
:root{
  --navy:#163566;
  --navy-deep:#12397a;
  --blue:#0054AA;
  --blue-mid:#0677BA;
  --blue-bright:#0b52c4;
  --sky:#6FCCEA;
  --sky-band:#8fdcf5;
  --pale:#E9F6FB;
  --red:#e3201b;
  --red-soft:#EB3D1F;
  --ink:#1d1d1f;
  --grey:#6b6f76;
  --line:#e3e7ee;
  --white:#ffffff;
  --head:"Saira",sans-serif;
  --body:"Open Sans",sans-serif;
}
*{box-sizing:border-box;margin:0;padding:0}
html,body{width:1200px;height:4946px;overflow:hidden}
body{position:relative;background:var(--white);font-family:var(--body);color:var(--ink)}
.abs{position:absolute}
.h2{font-family:var(--head);font-size:46px;line-height:1;text-transform:uppercase;letter-spacing:.5px;text-align:center}
.h2 b{font-weight:900;font-style:italic}
.h2 span{font-weight:500}
.rule{width:70px;height:4px;background:var(--red);margin:0 auto}
.btn{display:inline-flex;align-items:center;justify-content:center;font-family:var(--head);font-weight:800;font-size:14px;color:#fff;text-transform:uppercase;border-radius:6px;height:48px;padding:0 20px;letter-spacing:.2px}
.btn.red{background:var(--red)}
.btn.blue{background:var(--blue)}
.more{font-size:12px;font-weight:700;color:var(--red);text-decoration:underline;text-transform:uppercase}

/* top bar + hero */
.topbar{left:0;top:0;width:1200px;height:31px;background:var(--navy);z-index:3}
.topbar .social{left:112px;top:9px;display:flex;gap:12px}
.topbar .social i{display:block;width:12px;height:12px;border-radius:50%;background:#fff}
.topbar nav{right:112px;top:8px;display:flex;gap:22px;font-size:11px;font-weight:700;color:#fff;text-transform:uppercase}
.hero{left:0;top:31px;width:1200px;height:515px;background:linear-gradient(90deg,#1a1d22 0%,#2f3338 35%,#5d6268 62%,#8a8f93 100%)}
.hero .shade{inset:0;background:linear-gradient(90deg,rgba(10,12,16,.75) 0%,rgba(10,12,16,.35) 55%,rgba(10,12,16,0) 100%)}
.brand{font-family:var(--head);font-weight:800;font-size:17px;line-height:1.05;color:#fff;text-transform:uppercase;display:flex;align-items:center;gap:8px}
.brand i{display:block;width:14px;height:14px;border-radius:50%;background:var(--red)}
.hero .brand{left:112px;top:58px;width:150px}
.mainnav{left:270px;top:42px;display:flex;gap:18px;font-size:13px;font-weight:700;color:#fff;text-transform:uppercase}
.mainnav .on{color:var(--sky)}
.navtools{left:1024px;top:38px;display:flex;gap:26px}
.hero .kicker{left:112px;top:141px;font-size:19px;color:#fff;text-transform:uppercase}
.hero h1{left:112px;top:180px;font-family:var(--head);font-weight:900;font-style:italic;font-size:60px;line-height:62px;color:#fff;text-transform:uppercase}
.hero .btn{left:112px;top:392px;height:48px;font-size:14px}
.dots{left:612px;top:453px;display:flex;gap:6px;align-items:center}
.dots i{display:block;width:10px;height:10px;border-radius:50%;border:2px solid #fff}
.dots i.on{width:14px;height:14px;background:var(--blue);border-color:#fff}

/* about */
.about{left:0;top:546px;width:1200px;height:697px}
.about .portrait{left:112px;top:90px}
.about .copy{left:620px;top:92px;width:470px}
.about .mark{width:40px;height:4px;background:var(--red);margin-bottom:6px}
.about h2{font-family:var(--head);font-size:46px;line-height:1;color:var(--blue);text-transform:uppercase}
.about h2 b{font-weight:900;font-style:italic}
.about h2 span{font-weight:500}
.about .lede{margin-top:38px;font-size:15px;font-weight:700;font-style:italic;line-height:24px;text-transform:uppercase;color:var(--ink)}
.about p.t{margin-top:14px;font-size:14.5px;line-height:24px;color:var(--grey)}
.about .sign{margin-top:20px;width:170px;height:80px;border-radius:6px;background:linear-gradient(90deg,#eef3fa,#f7f9fc)}
.about .actions{margin-top:22px;display:flex;gap:12px}

/* services */
.services{left:0;top:1243px;width:1200px;height:600px}
.services .band{left:0;top:0;width:1200px;height:357px;background:radial-gradient(ellipse at 50% 20%,#1d56b0 0%,#123f8e 50%,#0c2f6d 100%)}
.services .h2{position:absolute;left:0;top:50px;width:1200px;color:#fff}
.services .rule{position:absolute;left:565px;top:104px;background:#fff}
.scard{top:167px;width:308px;height:383px;background:#fff;box-shadow:0 8px 22px rgba(12,40,90,.15);border-radius:4px;overflow:hidden}
.scard .ph{height:307px}
.scard .lbl{height:76px;display:flex;align-items:center;justify-content:center;font-size:14.5px;font-weight:700;text-transform:uppercase;letter-spacing:.3px}
.scard.active .lbl{background:var(--blue);color:#fff}

/* connect */
.connect{left:0;top:1843px;width:1200px;height:530px}
.connect .h2{position:absolute;left:0;top:37px;width:1200px;color:var(--blue)}
.connect .sub{left:0;top:92px;width:1200px;text-align:center;font-family:var(--head);font-weight:600;font-size:12.5px;text-transform:uppercase;color:var(--ink)}
.connect .rule{position:absolute;left:565px;top:120px}
.ccard{top:173px;width:232px;height:262px;background:#fff;box-shadow:0 4px 16px rgba(12,40,90,.12);border-radius:4px;text-align:center;padding:20px 14px 0}
.ccard .ic{width:74px;height:74px;border-radius:50%;border:2px solid #e6e8ec;margin:0 auto;display:flex;align-items:center;justify-content:center}
.ccard h3{margin-top:20px;font-size:12.5px;font-weight:700;text-transform:uppercase}
.ccard p{margin-top:8px;font-size:13px;line-height:20px;color:var(--grey)}
.ccard .more{display:inline-block;margin-top:6px}
.arrow{width:36px;height:36px;border-radius:50%;display:flex;align-items:center;justify-content:center}
.arrow.fill{background:var(--blue)}
.arrow.ring{border:2px solid var(--blue)}

/* partners */
.partners{left:0;top:2373px;width:1200px;height:443px;background:var(--sky-band)}
.partners .h2{position:absolute;left:0;top:50px;width:1200px;color:var(--blue)}
.partners .rule{position:absolute;left:565px;top:106px}
.badge{width:186px;height:75px;background:#fff;border-radius:5px;display:flex;align-items:center;justify-content:center}
.badge i{display:block;width:120px;height:22px;border-radius:4px;background:#c9d2dd}
.partners .btn{position:absolute;left:537px;top:336px;width:126px}

/* easy */
.easy{left:0;top:2816px;width:1200px;height:570px;background:var(--pale)}
.easy .h2{position:absolute;left:0;top:90px;width:1200px;color:var(--blue)}
.easy .rule{position:absolute;left:565px;top:152px}
.ecard{top:227px;width:270px;height:273px;background:#fff;border-radius:4px;text-align:center;padding:74px 18px 0;box-shadow:0 4px 16px rgba(12,40,90,.08)}
.ecard.active{background:var(--navy-deep);color:#fff}
.ecard .num{position:absolute;left:87px;top:-33px;width:96px;height:96px;border-radius:50%;background:var(--navy-deep);border:4px solid var(--pale);color:#fff;font-family:var(--head);font-weight:900;font-style:italic;font-size:40px;display:flex;align-items:center;justify-content:center}
.ecard h3{font-size:15px;font-weight:700;text-transform:uppercase}
.ecard p{margin-top:10px;font-size:14px;line-height:25px;color:var(--grey)}
.ecard.active p{color:#dfe7f5}
.ecard.active .more{color:#fff}

/* testimonials */
.testi{left:0;top:3386px;width:1200px;height:490px}
.testi .h2{position:absolute;left:0;top:80px;width:1200px;color:var(--blue)}
.testi .rule{position:absolute;left:565px;top:138px}
.testi .dot{left:576px;top:184px;width:48px;height:48px;border-radius:50%;background:#e8eef7}
.testi blockquote{left:220px;top:250px;width:760px;text-align:center;font-style:italic;font-size:15px;line-height:26px;color:var(--grey)}
.testi .who{left:0;top:357px;width:1200px;text-align:center;font-size:14px;font-weight:700;color:var(--blue);text-transform:uppercase}
.testi .stars{left:0;top:378px;width:1200px;text-align:center;color:#f4c20d;font-size:18px;letter-spacing:6px}

/* quote */
.quote{left:0;top:3876px;width:1200px;height:486px}
.quote .ph{left:0;top:0;width:594px;height:486px;background:linear-gradient(135deg,#d9d3c4 0%,#8e8a7d 40%,#3a3a36 100%)}
.quote .panel{left:594px;top:0;width:606px;height:486px;background:linear-gradient(160deg,#0d57cc 0%,#0b4bb6 60%,#0a3f9c 100%)}
.quote h2{left:643px;top:40px;font-family:var(--head);font-size:44px;color:#fff;text-transform:uppercase;line-height:1}
.quote h2 b{font-weight:900;font-style:italic}
.quote h2 span{font-weight:500}
.field{background:#fff;border-radius:3px;font-size:12.5px;color:#8a8f96;padding:14px 12px}
.quote .btn{left:643px;top:382px;width:124px;height:47px}

/* newsletter + footer */
.foot{left:0;top:4362px;width:1200px;height:584px;background:var(--navy)}
.foot .h2{position:absolute;left:0;top:78px;width:1200px;color:#fff}
.subscribe{left:270px;top:213px;width:675px;height:54px;background:#fff;border-radius:4px}
.subscribe .ph{left:20px;top:18px;font-size:13px;color:#8a8f96}
.subscribe .btn{position:absolute;right:6px;top:5px;height:44px;width:124px}
.foot .brand{left:112px;top:305px;width:160px;font-size:26px;justify-content:center;text-align:center;flex-direction:column}
.foot .soc{top:440px;width:40px;height:40px;border-radius:50%}
.col{top:268px}
.col h4{font-family:var(--head);font-weight:800;font-size:19px;color:#fff;text-transform:uppercase;margin-bottom:14px}
.col li{list-style:none;font-size:15px;color:#fff;height:42px}
.contact{left:796px;top:272px}
.contact .row{display:flex;gap:16px;margin-top:22px;color:#fff}
.contact .ci{width:40px;height:40px;border-radius:50%;background:var(--blue-bright);display:flex;align-items:center;justify-content:center;flex:none}
.contact .row b{display:block;font-size:14px;text-transform:uppercase}
.contact .row span{font-size:15px;line-height:20px}
.foot .divider{left:112px;top:533px;width:976px;height:1px;background:rgba(255,255,255,.25)}
.foot .copy{left:0;top:550px;width:1200px;text-align:center;font-size:13px;color:#fff}
</style>
</head>
<body>

<!-- Top bar -->
<div class="abs topbar">
  <div class="abs social"><i></i><i></i></div>
  <nav class="abs"><span>About</span><span>Project Consulting</span><span>Contact</span></nav>
</div>

<!-- Hero -->
<section class="abs hero">
  <div class="abs" style="inset:0" role="img" aria-label="Modern home entrance with glass-paned front door and smart lock"></div>
  <div class="abs shade"></div>
  <div class="abs brand"><i></i>Maple Wren Systems</div>
  <nav class="abs mainnav">
    <span class="on">Home</span><span>Electronic Security</span><span>Audio + Video</span><span>Networking + Communication</span><span>Cabling</span>
  </nav>
  <div class="abs navtools">
    <svg width="18" height="18" viewBox="0 0 18 18"><circle cx="9" cy="5" r="4" fill="#fff"/><path d="M1 17c0-4 4-6 8-6s8 2 8 6z" fill="#fff"/></svg>
    <svg width="18" height="18" viewBox="0 0 18 18"><circle cx="7.5" cy="7.5" r="5.5" stroke="#fff" stroke-width="2.4" fill="none"/><path d="M12 12l5 5" stroke="#fff" stroke-width="2.4"/></svg>
  </div>
  <div class="abs kicker">Proudly Serving Middle Tennessee</div>
  <h1 class="abs">Safer. Smarter.<br>Faster. Homes<br>Businesses</h1>
  <a class="abs btn red">Request a Quote</a>
  <div class="abs dots"><i></i><i class="on"></i><i></i></div>
</section>

<!-- About -->
<section class="abs about">
  <svg class="abs portrait" width="448" height="516" viewBox="0 0 448 516">
    <path d="M0 22 L448 22 L448 200 C440 360 330 460 224 516 C118 460 8 360 0 200 Z" fill="#e3201b"/>
    <path d="M28 0 L420 0 L420 190 C412 340 318 436 224 486 C130 436 36 340 28 190 Z" fill="#2b2f36"/>
    <path d="M28 0 L420 0 L420 190 C412 340 318 436 224 486 C130 436 36 340 28 190 Z" fill="url(#pg)" role="img" aria-label="Portrait of founder Elliot Marsh in a navy suit and bow tie"/>
    <defs><radialGradient id="pg" cx="50%" cy="45%" r="60%"><stop offset="0" stop-color="#6a6e75"/><stop offset="1" stop-color="#1f2227"/></radialGradient></defs>
  </svg>
  <div class="abs copy">
    <div class="mark"></div>
    <h2><b>About</b> <span>Us</span></h2>
    <p class="lede">I founded Maple Wren Systems to bring together technology and honest, reliable service.</p>
    <p class="t">I’m proud to call Tennessee home and even prouder to help keep its homes and businesses secure.</p>
    <p class="t">Whether it’s protecting or elevating your space, my goal is to make technology work for you.</p>
    <p class="t">Think of us as your friendly, neighborhood tech expert—here to safeguard what matters most.</p>
    <div class="sign" role="img" aria-label="Handwritten signature of Elliot Marsh"></div>
    <div class="actions"><a class="btn red">Tell Us How We Can Help</a><a class="btn blue">Read More</a></div>
  </div>
</section>

<!-- Services -->
<section class="abs services">
  <div class="abs band"></div>
  <h2 class="h2"><b>Our</b> <span>Services</span></h2>
  <div class="rule"></div>
  <div class="abs scard" style="left:112px">
    <div class="ph" role="img" aria-label="Woman using a wall-mounted security keypad" style="background:linear-gradient(135deg,#e7e3de,#b49a86 60%,#7d6656)"></div>
    <div class="lbl">Affordable Security</div>
  </div>
  <div class="abs scard active" style="left:446px">
    <div class="ph" role="img" aria-label="Home theatre room with a large screen" style="background:linear-gradient(160deg,#c9b8a3,#7a6b5b 55%,#3a332c)"></div>
    <div class="lbl">Enviable Entertainment</div>
  </div>
  <div class="abs scard" style="left:780px">
    <div class="ph" role="img" aria-label="Team on a video conference in a meeting room" style="background:linear-gradient(150deg,#d5dbe2,#8a939c 55%,#2e3338)"></div>
    <div class="lbl">Connected Businesses</div>
  </div>
</section>

<!-- Connect + Protect -->
<section class="abs connect">
  <h2 class="h2"><b>Connect + Protect</b> <span>Your World</span></h2>
  <div class="abs sub">Protect your people, assets, and information from whatever comes.</div>
  <div class="rule"></div>
  <div class="abs arrow fill" style="left:45px;top:290px"><svg width="12" height="12" viewBox="0 0 12 12"><path d="M8 1L3 6l5 5" stroke="#fff" stroke-width="2.2" fill="none"/></svg></div>
  <div class="abs arrow ring" style="left:1118px;top:290px"><svg width="12" height="12" viewBox="0 0 12 12"><path d="M4 1l5 5-5 5" stroke="#0054AA" stroke-width="2.2" fill="none"/></svg></div>

  <div class="abs ccard" style="left:112px">
    <div class="ic"><svg width="40" height="30" viewBox="0 0 40 30" fill="none" stroke="#222" stroke-width="2"><circle cx="20" cy="15" r="3" fill="#222"/><path d="M13 8a10 10 0 000 14M27 8a10 10 0 010 14M8 4a16 16 0 000 22M32 4a16 16 0 010 22"/></svg></div>
    <h3>Entry &amp; Motion Sensors</h3>
    <p>Pair text with an icon to focus on your chosen product, collection, or blog post.</p>
    <a class="more">Learn More</a>
  </div>
  <div class="abs ccard" style="left:360px">
    <div class="ic"><svg width="30" height="42" viewBox="0 0 30 42" fill="none" stroke="#222" stroke-width="2"><rect x="7" y="4" width="16" height="34" rx="8"/><circle cx="15" cy="13" r="3"/><circle cx="15" cy="27" r="4"/></svg></div>
    <h3>Video Doorbells</h3>
    <p>Pair text with an icon to focus on your chosen product, collection, or blog post.</p>
    <a class="more">Learn More</a>
  </div>
  <div class="abs ccard" style="left:608px">
    <div class="ic"><svg width="40" height="34" viewBox="0 0 40 34" fill="none" stroke="#222" stroke-width="2"><path d="M4 4h32v6H4z"/><path d="M8 10c0 10 5 18 12 18s12-8 12-18"/><circle cx="20" cy="18" r="5"/><circle cx="20" cy="18" r="2" fill="#222"/></svg></div>
    <h3>Security Cameras</h3>
    <p>Pair text with an icon to focus on your chosen product, collection, or blog post.</p>
    <a class="more">Learn More</a>
  </div>
  <div class="abs ccard" style="left:856px">
    <div class="ic"><svg width="38" height="36" viewBox="0 0 38 36" fill="none" stroke="#222" stroke-width="2"><ellipse cx="19" cy="25" rx="8" ry="7"/><circle cx="9" cy="15" r="3.5"/><circle cx="29" cy="15" r="3.5"/><circle cx="14" cy="7" r="3.5"/><circle cx="24" cy="7" r="3.5"/></svg></div>
    <h3>Pet-Friendly</h3>
    <p>Pair text with an icon to focus on your chosen product, collection, or blog post.</p>
    <a class="more">Learn More</a>
  </div>
</section>

<!-- Partners -->
<section class="abs partners">
  <h2 class="h2"><b>Service</b> <span>Partners</span></h2>
  <div class="rule"></div>
  <div class="abs badge" style="left:112px;top:150px"><i></i></div>
  <div class="abs badge" style="left:310px;top:150px"><i></i></div>
  <div class="abs badge" style="left:508px;top:150px"><i></i></div>
  <div class="abs badge" style="left:706px;top:150px"><i></i></div>
  <div class="abs badge" style="left:904px;top:150px"><i></i></div>
  <div class="abs badge" style="left:207px;top:238px"><i></i></div>
  <div class="abs badge" style="left:405px;top:238px"><i></i></div>
  <div class="abs badge" style="left:603px;top:238px"><i></i></div>
  <div class="abs badge" style="left:801px;top:238px;background:#eef1f4"><i></i></div>
  <a class="btn red">View More</a>
</section>

<!-- Easy steps -->
<section class="abs easy">
  <h2 class="h2"><b>A Safer Home or Business</b> <span>Is As Easy</span></h2>
  <div class="rule"></div>
  <div class="abs ecard" style="left:148px">
    <div class="num">01</div>
    <h3>Build an Instant Quote</h3>
    <p>Our live-estimate builder will guide you through a few questions to help us understand your needs.</p>
    <a class="more">Learn More</a>
  </div>
  <div class="abs ecard active" style="left:466px">
    <div class="num">02</div>
    <h3>Schedule Installation</h3>
    <p>Our live-estimate builder will guide you through a few questions to help us understand your needs.</p>
    <a class="more">Learn More</a>
  </div>
  <div class="abs ecard" style="left:783px">
    <div class="num">03</div>
    <h3>Stay Secure 24/7</h3>
    <p>Our live-estimate builder will guide you through a few questions to help us understand your needs.</p>
    <a class="more">Learn More</a>
  </div>
</section>

<!-- Testimonials -->
<section class="abs testi">
  <h2 class="h2"><b>Client</b> <span>Testimonials</span></h2>
  <div class="rule"></div>
  <div class="abs dot"></div>
  <div class="abs arrow fill" style="left:156px;top:266px"><svg width="12" height="12" viewBox="0 0 12 12"><path d="M8 1L3 6l5 5" stroke="#fff" stroke-width="2.2" fill="none"/></svg></div>
  <div class="abs arrow ring" style="left:1002px;top:266px"><svg width="12" height="12" viewBox="0 0 12 12"><path d="M4 1l5 5-5 5" stroke="#0054AA" stroke-width="2.2" fill="none"/></svg></div>
  <blockquote class="abs">“I couldn’t be more impressed with the service we received for our condo’s security system upgrade. The team was professional, efficient, and incredibly knowledgeable, providing us with state-of-the-art solutions that have significantly enhanced the safety and security of our building. Highly recommend their services!”</blockquote>
  <div class="abs who">–Harbor Line Property Group</div>
  <div class="abs stars">★★★★★</div>
</section>

<!-- Request a quote -->
<section class="abs quote">
  <div class="abs ph" role="img" aria-label="Woman on a video call at a desktop computer"></div>
  <div class="abs panel"></div>
  <h2 class="abs"><b>Request</b> <span>A Quote</span></h2>
  <div class="abs field" style="left:643px;top:151px;width:194px;height:45px">First Name</div>
  <div class="abs field" style="left:846px;top:151px;width:194px;height:45px">Last Name</div>
  <div class="abs field" style="left:643px;top:207px;width:194px;height:45px">Email</div>
  <div class="abs field" style="left:846px;top:207px;width:194px;height:45px">Phone No</div>
  <div class="abs field" style="left:643px;top:264px;width:397px;height:97px">Message</div>
  <a class="abs btn red">Submit</a>
</section>

<!-- Newsletter + footer -->
<footer class="abs foot">
  <h2 class="h2"><b>Subscribe To</b> <span>Our Newsletter</span></h2>
  <div class="abs subscribe">
    <div class="abs ph">Your Email</div>
    <a class="btn red">Subscribe</a>
  </div>
  <div class="abs brand">Maple Wren Systems<i></i></div>
  <div class="abs soc" style="left:170px;background:var(--red)"></div>
  <div class="abs soc" style="left:222px;border:2px solid #fff"></div>

  <div class="abs col" style="left:362px">
    <h4>Residential</h4>
    <ul><li>Home Security</li><li>Smart Homes</li><li>Home Theatres + A/V</li><li>WiFi</li><li>Cabling</li></ul>
  </div>
  <div class="abs col" style="left:587px">
    <h4>Commercial</h4>
    <ul><li>Audio Video</li><li>Cabling</li><li>Communication</li><li>Electronic Security</li><li>Project Consulting</li></ul>
  </div>
  <div class="abs contact">
    <h4 style="font-family:var(--head);font-weight:800;font-size:19px;color:#fff;text-transform:uppercase">Contact Us</h4>
    <div class="row">
      <div class="ci"><svg width="18" height="18" viewBox="0 0 24 24"><path d="M6.6 10.8a15 15 0 006.6 6.6l2.2-2.2a1 1 0 011-.25 11.4 11.4 0 003.6.57 1 1 0 011 1V20a1 1 0 01-1 1A17 17 0 013 4a1 1 0 011-1h3.5a1 1 0 011 1c0 1.25.2 2.45.57 3.6a1 1 0 01-.25 1z" fill="#fff"/></svg></div>
      <div><b>Phone No:</b><span>555.014.2290</span></div>
    </div>
    <div class="row">
      <div class="ci"><svg width="18" height="14" viewBox="0 0 18 14"><rect x="0" y="0" width="18" height="14" rx="2" fill="#fff"/><path d="M1 1l8 6 8-6" stroke="#0b52c4" stroke-width="1.6" fill="none"/></svg></div>
      <div><b>Email:</b><span>info@maplewren.example</span></div>
    </div>
    <div class="row">
      <div class="ci"><svg width="16" height="20" viewBox="0 0 16 20"><path d="M8 0a8 8 0 018 8c0 6-8 12-8 12S0 14 0 8a8 8 0 018-8z" fill="#fff"/><circle cx="8" cy="8" r="3" fill="#0b52c4"/></svg></div>
      <div><b>Location:</b><span>482 Alder Ridge Rd. Suite<br>2-210 Brookhaven, TN 37000</span></div>
    </div>
  </div>
  <div class="abs divider"></div>
  <div class="abs copy">©2024 Maple Wren Systems. All rights reserved. Site Terms | Privacy Policy</div>
</footer>

</body>
</html>
```